Title: Iron Ledger Sub: She never leaves the harbor - Book cover

I need a complete book cover, front, spine, and back.

Religions Book

This book is more about the Title so it should be strong and serious.

Like the color Deep Red and black, blue. Deep purple
Avoid greens, orange, yellows.

Maybe a picture of a strong hand on the Bible. OR someone yelling.

If any pictures are used they must be 100% royalty free with proof or a buyout of image.

I have attached a couple of designs that the client likes. Just as a reference. The exception they DIDN'T like the pictures in the book cover.

Please ask any questions to clarify.

Please see the file I just uploaded called 'Book Cover samples.png" The clients likes the Title: Salt and Ember" the best. Please create a design something closer to this. The like how the title jumps off the page with a 2D look.

Again the Title must standout, and any use of images must be a secondary to the design.

I am happy with we the designs that have been submitted so far.

I hope this helps you get closer.

Thank you

First of all I want to thank you for all of your designs. At the beginning the client thought he would like a picture that represented the title. But after looking at all of the designs. He has now decided NOT to have any pictures.

Here is what he wants

1. BOLD Font (San Serif only) no fancy versions for the Title "IRON LEDGER" in uppercase. The title font should have some dimension to it to appear 2D or 3D looks. Shiny look. It needs to looks like it jumping off the page.

2. The subtitle right below the title in San Serif font)

3. Background solid color either black, dark red, or dark blue. The background can be slightly textured or gradation fill, etc.

4. The cover must have a strong and bold statement.

Thank you again.

Please use this photo on the back cover.

Thank you

Requirements
Should not have
• A picture that over powers the Title.

```html
<!DOCTYPE html>
<html lang="en">
<head>
<meta charset="utf-8">
<title>Iron Ledger – Book Cover</title>
<link rel="stylesheet" href="https://fonts.googleapis.com/css2?family=Cinzel:wght@400;600;700&family=Montserrat:wght@500;600;700;800&display=swap">
<style>
  :root {
    --wine-center: #6e1c2a;
    --wine-mid: #521320;
    --wine-edge: #2e0810;
    --ink-white: #ffffff;
    --gold-light: #fbe9b8;
    --gold-mid: #d6ac62;
    --gold-deep: #9b7134;
    --fold-line: rgba(255, 235, 230, 0.35);
    --author-panel: #3a0a13;
  }
  * { margin: 0; padding: 0; box-sizing: border-box; }
  html, body {
    width: 1200px;
    height: 847px;
    overflow: hidden;
    background: var(--wine-edge);
  }
  .cover {
    position: relative;
    width: 1200px;
    height: 847px;
    overflow: hidden;
    font-family: "Cinzel", "Times New Roman", serif;
    color: var(--ink-white);
    background: radial-gradient(ellipse at 60% 45%, var(--wine-center) 0%, var(--wine-mid) 50%, var(--wine-edge) 100%);
  }
  .title-face { font-family: "Montserrat", "Helvetica Neue", Arial, sans-serif; }
  .fold { position: absolute; top: 0; width: 1px; height: 847px; background: var(--fold-line); }
  .fold--left { left: 543px; }
  .fold--right { left: 657px; }

  .gold-rule {
    position: absolute;
    height: 5px;
    background: linear-gradient(90deg, var(--gold-deep), var(--gold-light) 45%, var(--gold-mid) 75%, var(--gold-deep));
  }

  /* Back cover */
  .back-title {
    position: absolute;
    left: 0;
    width: 543px;
    text-align: center;
    font-weight: 700;
    line-height: 1;
  }
  .back-title--top { top: 41px; font-size: 118px; }
  .back-title--bottom { top: 168px; font-size: 70px; }
  .back-rule { left: 123px; top: 160px; width: 293px; }

  .back-blurb {
    position: absolute;
    left: 46px;
    top: 296px;
    width: 451px;
    font-size: 15.5px;
    line-height: 21.6px;
    text-align: justify;
    hyphens: auto;
    -webkit-hyphens: auto;
  }
  .author-photo {
    float: left;
    width: 190px;
    height: 210px;
    margin: 2px 6px 4px 0;
    background: linear-gradient(160deg, #f4f2f0 0%, #e2cbbb 45%, #3b4a86 100%);
  }
  .website {
    position: absolute;
    left: 50px;
    top: 742px;
    width: 442px;
    height: 44px;
    display: flex;
    align-items: center;
    justify-content: center;
    background: linear-gradient(180deg, var(--gold-light), var(--gold-mid) 60%, var(--gold-deep));
    color: #6a1424;
    font-weight: 700;
    font-size: 24px;
    letter-spacing: 0.5px;
  }

  /* Spine */
  .spine-title {
    position: absolute;
    left: 566px;
    top: 52px;
    writing-mode: vertical-rl;
    font-size: 50px;
    font-weight: 600;
    line-height: 1;
    white-space: nowrap;
  }
  .spine-rule { left: 628px; top: 50px; width: 5px; height: 450px;
    background: linear-gradient(180deg, var(--gold-deep), var(--gold-light) 45%, var(--gold-mid) 75%, var(--gold-deep)); }
  .spine-author {
    position: absolute;
    left: 582px;
    top: 570px;
    writing-mode: vertical-rl;
    font-size: 26px;
    line-height: 1;
    white-space: nowrap;
  }

  /* Front cover */
  .front-title {
    position: absolute;
    left: 657px;
    width: 543px;
    text-align: center;
    font-weight: 800;
    line-height: 1;
    background: linear-gradient(180deg, var(--gold-light) 0%, #f2d393 35%, var(--gold-mid) 60%, var(--gold-deep) 100%);
    -webkit-background-clip: text;
    background-clip: text;
    color: transparent;
    filter: drop-shadow(2px 3px 2px rgba(20, 0, 5, 0.7)) drop-shadow(0 0 6px rgba(255, 120, 130, 0.35));
  }
  .front-title--top { top: 162px; font-size: 176px; letter-spacing: -2px; }
  .front-title--bottom { top: 352px; font-size: 108px; }
  .front-rule { left: 700px; top: 343px; width: 445px; height: 7px; }

  .subtitle {
    position: absolute;
    left: 677px;
    top: 622px;
    width: 503px;
    text-align: center;
    font-family: "Montserrat", "Helvetica Neue", Arial, sans-serif;
    font-size: 28px;
    font-weight: 600;
    text-shadow: 2px 2px 3px rgba(0, 0, 0, 0.6);
  }
  .author-plate {
    position: absolute;
    left: 783px;
    top: 778px;
    width: 282px;
    height: 75px;
    border-radius: 12px 12px 0 0;
    background: var(--author-panel);
    display: flex;
    align-items: center;
    justify-content: center;
    padding-bottom: 8px;
    font-size: 28px;
  }
</style>
</head>
<body>
  <main class="cover">
    <section class="back-cover">
      <h2 class="back-title title-face back-title--top">IRON</h2>
      <div class="gold-rule back-rule"></div>
      <h2 class="back-title title-face back-title--bottom">LEDGER</h2>
      <div class="back-blurb">
        <div class="author-photo" role="img" aria-label="Portrait photo of the author"></div>
        <p>Lorem ipsum dolor sit amet, consectetur adipiscing elit. In eget nibh eu nulla imperdiet feugiat. Cum sociis natoque penatibus et magnis dis parturient montes, nascetur ridiculus mus. Sed in ante consectetur sem feugiat eleifend ac vel enim. Fusce quis est in nisi pretium facilisis. Etiam adipiscing interdum libero, aliquam aliquet orci cursus quis. Aliquam lobortis lacus quis purus tempor pretium. Aliquam ut placerat dui. Integer dictum risus dui, sit amet consequat nunc blandit ac. Aenean porttitor eros at felis ornare feugiat. Aenean sit amet nulla sem. Proin sem neque, imperdiet aliquet pulvinar et, hendrerit nec augue. Interdum et malesuada fames ac ante ipsum primis in faucibus.</p>
      </div>
      <div class="website">WWW.MARTINCALDWELL.COM</div>
    </section>

    <div class="fold fold--left"></div>
    <section class="spine">
      <span class="spine-title title-face">IRON LEDGER</span>
      <div class="spine-rule gold-rule"></div>
      <span class="spine-author">Martin Caldwell</span>
    </section>
    <div class="fold fold--right"></div>

    <section class="front-cover">
      <h1 class="front-title title-face front-title--top">IRON</h1>
      <div class="gold-rule front-rule"></div>
      <h1 class="front-title title-face front-title--bottom">LEDGER</h1>
      <p class="subtitle">She Never Leaves the Harbor</p>
      <div class="author-plate">Martin Caldwell</div>
    </section>
  </main>
</body>
</html>
```